Brevard Trade Partners - we are Asian sourcing agents

We are sourcing agents based in the USA and we act as sourcing agents for clients in throughout the world. We focus primarily on custom sewn goods. So basically companies who do not have the in-house expertise to do it themselves, come to us and have us find suitable factories in Asia to do the production. We are middlemen. We find the factories...quote the project...manage the quality control and then deliver the goods directly to our customer's door. We pride ourselves in making the communication very easy and precise.

Current page is www.brevardtradepartners.com

I am not happy w/ the overall look. The spacing...the photos, the fonts...the design elements...the pictures. I want a cool, crisp design that conveys professionalism and clearly depicts/explains what we do.

Requirements
Must have
• use my logo....I like it...it was designed by someone on this website.
Nice to have
• a video/animation of the entire process would be wonderful. Showing initial contact with our office in the USA...then to my correspondence with my offices in Taiwan and in Hong Kong...and then back and fort w/ the customer.....and then between my people in Hong Kong/Taiwan with the local factories......and then a quote is generated and sent to my client......to samples being made and sent for approval.....to a PO being generated......to final samples being sent.....to the order being shipped and delivered to the clients warehouse. I was thinking of an animation showing arrows and text showing the back and forth communication and explaining how the process flows.

```html
<!DOCTYPE html>
<html lang="en">
<head>
<meta charset="utf-8">
<title>Brevard Trade Partners – Asian Outsourcing Made Easy</title>
<link href="https://fonts.googleapis.com/css2?family=Figtree:wght@400;500;600;700;800&display=swap" rel="stylesheet">
<style>
:root{
  --green:#5f8a17;
  --green-dark:#4f7512;
  --navy:#141a4d;
  --text:#555a60;
  --muted:#777;
  --line:#dcdcdc;
  --footer-bg:#ececec;
  --white:#fff;
}
*{margin:0;padding:0;box-sizing:border-box}
html,body{width:1200px;height:2442px;overflow:hidden}
body{font-family:'Figtree',sans-serif;color:var(--text);background:var(--white);position:relative}
.abs{position:absolute}
ul{list-style:none}

/* header */
.site-header{position:absolute;left:0;top:0;width:1200px;height:106px;background:var(--white);border-top:4px solid var(--green);box-shadow:0 2px 4px rgba(0,0,0,.12);z-index:2}
.brand{position:absolute;left:98px;top:32px;font-weight:800;font-size:27px;color:var(--navy);letter-spacing:.5px;line-height:1}
.brand-sub{display:block;font-size:15px;color:var(--navy);letter-spacing:1.5px;margin-top:4px;font-weight:800}
.main-nav a{position:absolute;top:44px;font-size:15px;font-weight:500;color:#444;text-decoration:none;letter-spacing:.5px;transform:translateX(-50%);white-space:nowrap}
.main-nav a.active{color:var(--green)}
.nav-underline{position:absolute;left:519px;top:98px;width:48px;height:6px;background:var(--green)}

/* hero */
.hero{position:absolute;left:0;top:106px;width:1200px;height:496px;background:linear-gradient(180deg,#b6aec4 0%,#9c93a8 35%,#7b7464 55%,#5b6a3e 80%,#4a5a2f 100%)}
.hero-title{position:absolute;top:178px;width:100%;text-align:center;color:var(--white);font-weight:800;font-size:37px;letter-spacing:.5px}
.hero-sub{position:absolute;top:230px;width:100%;text-align:center;color:var(--white);font-size:27px;font-weight:400}
.hero-btn{position:absolute;left:484px;top:286px;width:232px;height:52px;background:var(--navy);color:var(--white);font-weight:600;font-size:16px;display:flex;align-items:center}
.hero-btn span{width:180px;text-align:center}
.hero-btn i{width:52px;height:52px;background:var(--green);display:flex;align-items:center;justify-content:center}
.hero-arrow{position:absolute;top:213px;width:66px;height:66px;border-radius:50%;background:rgba(60,60,60,.55);display:flex;align-items:center;justify-content:center}

/* section headings */
.section-title{position:absolute;width:100%;text-align:center;color:var(--navy);font-weight:700;font-size:23px;letter-spacing:.3px}

/* product cards */
.product-card{position:absolute;top:700px;width:187px;height:256px;border:1px solid var(--line);text-align:center}
.product-media{position:absolute;left:28px;top:18px;width:130px;height:80px;border-radius:6px}
.product-name{position:absolute;top:124px;width:100%;font-size:19px;font-weight:500;color:var(--navy)}
.product-text{position:absolute;top:158px;left:10px;right:10px;font-size:13px;line-height:19px;color:var(--muted)}
.more-btn{position:absolute;left:52px;top:208px;width:83px;height:35px;background:var(--green);color:var(--white);font-size:13px;font-weight:600;display:flex;align-items:center;justify-content:center}

.how-lead{position:absolute;top:1045px;width:100%;text-align:center;color:var(--green);font-size:18px}
.how-text{position:absolute;left:215px;top:1075px;width:770px;text-align:center;font-size:13px;line-height:23px;color:#444}
.video{position:absolute;left:238px;top:1146px;width:724px;height:274px;background:linear-gradient(100deg,#3d6a8a 0%,#8a2a35 35%,#c8c2bd 60%,#33485f 100%)}
.play{position:absolute;left:323px;top:98px}

/* cta band */
.cta-band{position:absolute;left:0;top:1475px;width:1200px;height:207px;background:var(--green);text-align:center;color:var(--white)}
.cta-title{position:absolute;top:38px;width:100%;font-weight:700;font-size:23px}
.cta-sub{position:absolute;top:78px;width:100%;font-size:17px}
.cta-btn{position:absolute;left:506px;top:127px;width:187px;height:44px;background:var(--white);color:var(--green);font-weight:700;font-size:16px;display:flex;align-items:center;justify-content:center}

/* info columns */
.info-title{position:absolute;top:1750px;color:var(--navy);font-weight:700;font-size:23px}
.info-text{position:absolute;left:98px;top:1792px;width:600px;font-size:13px;line-height:24.5px;color:#444}
.divider{position:absolute;left:726px;top:1739px;width:2px;height:219px;background:#e4e4e4}
.bullet-list li{position:relative;padding-left:22px;font-size:13px;color:#444;line-height:25px}
.bullet-list li::before{content:"";position:absolute;left:0;top:8px;width:9px;height:9px;border:2px solid var(--green);border-radius:50%}
.bullet-list li::after{content:"";position:absolute;left:4px;top:12px;width:3px;height:3px;background:var(--green);border-radius:50%}

/* footer */
.site-footer{position:absolute;left:0;top:2014px;width:1200px;height:373px;background:var(--footer-bg)}
.footer-head{position:absolute;top:40px;color:var(--navy);font-size:16px;font-weight:500;line-height:26px}
.footer-list{position:absolute;top:82px}
.footer-list li{font-size:13px;line-height:24px;color:var(--muted)}
.footer-list li::before{top:7px}
.footer-list li::after{top:11px}
.contact{position:absolute;left:910px;top:82px;font-size:13px;line-height:24px;color:var(--muted)}
.contact .email{color:var(--green)}
.news-input{position:absolute;left:597px;top:260px;width:196px;height:36px;border:1px solid #ccc;background:var(--white);font-size:12px;color:#555;padding:10px 14px}
.news-btn{position:absolute;left:698px;top:309px;width:93px;height:34px;background:var(--green);color:var(--white);font-size:14px;font-weight:600;display:flex;align-items:center;justify-content:center}

.bottom-bar{position:absolute;left:0;top:2387px;width:1200px;height:55px;background:var(--navy);color:var(--white)}
.copyright{position:absolute;left:100px;top:20px;font-size:12px}
.social{position:absolute;top:13px;width:30px;height:30px;border:2px solid var(--white);border-radius:50%}
</style>
</head>
<body>

<header class="site-header">
  <div class="brand">BREVARD<span class="brand-sub">TRADE PARTNERS LLC</span></div>
  <nav class="main-nav">
    <a class="active" style="left:549px">HOME</a>
    <a style="left:709px">PRODUCT CATEGORIES</a>
    <a style="left:884px">ABOUT US</a>
    <a style="left:1037px">REQUEST QUOTE</a>
  </nav>
  <div class="nav-underline"></div>
</header>

<section class="hero" role="img" aria-label="Photo of the Great Wall of China winding over green hills under a hazy sky">
  <h1 class="hero-title">ASIAN OUTSOURCING MADE EASY!</h1>
  <p class="hero-sub">Custom Sewn Goods Made to Your Specifications</p>
  <div class="hero-btn"><span>REQUEST QUOTE</span><i><svg width="12" height="14" viewBox="0 0 12 14"><path d="M1 0 L11 7 L1 14Z" fill="#fff"/></svg></i></div>
  <div class="hero-arrow" style="left:16px"><svg width="18" height="28" viewBox="0 0 18 28"><path d="M15 2 L3 14 L15 26" stroke="#fff" stroke-width="4" fill="none"/></svg></div>
  <div class="hero-arrow" style="left:1118px"><svg width="18" height="28" viewBox="0 0 18 28"><path d="M3 2 L15 14 L3 26" stroke="#fff" stroke-width="4" fill="none"/></svg></div>
</section>

<h2 class="section-title" style="top:638px">SOURCING CUSTOM GOODS IN CHINA ( PRODUCTS )</h2>

<article class="product-card" style="left:98px">
  <div class="product-media" role="img" aria-label="Black messenger bag with red and grey stripes" style="background:linear-gradient(180deg,#3a3a3a,#1e1e1e)"></div>
  <h3 class="product-name">Bags</h3>
  <p class="product-text">Sed ut perspiciatilores unde omnis iste natuslo sreil.</p>
  <div class="more-btn">MORE</div>
</article>
<article class="product-card" style="left:302px">
  <div class="product-media" role="img" aria-label="Pair of black and grey winter gloves" style="background:linear-gradient(90deg,#2a2a2a,#c9c9c9)"></div>
  <h3 class="product-name">Gloves</h3>
  <p class="product-text">Sed ut perspiciatilores unde omnis iste natuslo sreil.</p>
  <div class="more-btn">MORE</div>
</article>
<article class="product-card" style="left:506px">
  <div class="product-media" role="img" aria-label="Row of colourful phone cases" style="background:linear-gradient(90deg,#3a2a8a,#8a2aa0,#c02050,#e07020,#e0b020)"></div>
  <h3 class="product-name">Cases</h3>
  <p class="product-text">Sed ut perspiciatilores unde omnis iste natuslo sreil.</p>
  <div class="more-btn">MORE</div>
</article>
<article class="product-card" style="left:710px">
  <div class="product-media" role="img" aria-label="Red, black and white golf bags" style="background:linear-gradient(90deg,#2a2a2a,#c0232f,#e8e8e8,#2a2a2a)"></div>
  <h3 class="product-name">Sporting Goods</h3>
  <p class="product-text">Sed ut perspiciatilores unde omnis iste natuslo sreil.</p>
  <div class="more-btn">MORE</div>
</article>
<article class="product-card" style="left:915px">
  <div class="product-media" role="img" aria-label="Quilted white and blue medical pad" style="background:linear-gradient(160deg,#e6e9f0,#9fb8e6)"></div>
  <h3 class="product-name">Medical</h3>
  <p class="product-text">Sed ut perspiciatilores unde omnis iste natuslo sreil.</p>
  <div class="more-btn">MORE</div>
</article>

<h2 class="section-title" style="top:999px">HOW IT WORKS</h2>
<p class="how-lead">Brevard Trade Partners has been sourcing custom sewn goods in Asia since 1998.</p>
<p class="how-text">We work with our clients by matching their unique production needs with the best possible China sewing factories. We manage the entire process from start to finish, by first identifying the best factories to quote each job.</p>
<div class="video" role="img" aria-label="Video still of a worker at a sewing machine in a garment factory">
  <svg class="play" width="78" height="78" viewBox="0 0 78 78"><circle cx="39" cy="39" r="36" fill="rgba(40,40,40,.45)" stroke="#fff" stroke-width="3"/><path d="M31 24 L56 39 L31 54Z" fill="#fff"/></svg>
</div>

<section class="cta-band">
  <h2 class="cta-title">OUTSOURCE YOUR SEWING NEEDS TO TRUSTED CONTRACTORS IN CHINA</h2>
  <p class="cta-sub">Please contact us for immediate consultation regarding your outsourcing project.</p>
  <div class="cta-btn">REQUEST QUOTE</div>
</section>

<h2 class="info-title" style="left:98px">DON'T GO AT IT ALONE!</h2>
<p class="info-text">Brevard Trade Partners has been sourcing custom sewn goods in Asia since 1998. We work with our clients by matching their unique production needs with the best possible China sewing factories. We manage the entire process from start to finish, by first identifying the best factories to quote each job. The next step is negotiating the best (fair) price possible. We complete the process by monitoring the quality of the goods during production, and then managing the ocean logistics, customs clearances and local delivery right to your door.</p>
<div class="divider"></div>
<h2 class="info-title" style="left:797px">WHAT YOU NEED TO KNOW</h2>
<ul class="bullet-list abs" style="left:788px;top:1791px">
  <li>Contract Sewing in China</li>
  <li>What is the Process?</li>
  <li>What the Minimum Order?</li>
  <li>Contract Outsourcing FAQ</li>
  <li>Outsourcing Case Study</li>
  <li>Custom Industrial Sewing in China</li>
</ul>

<footer class="site-footer">
  <h4 class="footer-head" style="left:99px">CUSTOM BAGS</h4>
  <ul class="bullet-list footer-list" style="left:97px">
    <li>Athletic Bags</li><li>Backpacks</li><li>Computer Bags</li><li>Cooler Bags</li><li>Cosmetic Bags</li><li>Handbags</li><li>Messenger Bags</li><li>Shopping Bags</li><li>Tool Bags</li><li>Travel Bags</li><li>Yoga Bags</li>
  </ul>
  <h4 class="footer-head" style="left:314px">CUSTOM COVERS</h4>
  <ul class="bullet-list footer-list" style="left:312px">
    <li>ATV Covers</li><li>Chair Covers</li><li>Equipment Covers</li><li>Golf Cart Covers</li><li>Motorcycle Covers</li><li>Outdoor Furniture Covers</li><li>Outdoor Grill Cover</li><li>Personal Watercraft Covers</li><li>Snowmobile Covers</li>
  </ul>
  <h4 class="footer-head" style="left:597px">CUSTOM MEDICAL<br>ACCESSORIES</h4>
  <ul class="bullet-list footer-list" style="left:595px;top:108px">
    <li>Medical Equipment Covers</li><li>Medical Pads</li><li>Medical Sheets &amp; Bedding Supplies</li><li>Oxygen Tank Cases and Bags</li>
  </ul>
  <h4 class="footer-head" style="left:597px;top:224px">NEWSLETTER</h4>
  <div class="news-input">Email Address:</div>
  <div class="news-btn">SUBMIT</div>
  <h4 class="footer-head" style="left:904px">US HEADQUARTERS</h4>
  <div class="contact">
    Brevard Trade Partners, LLC<br>48 Harbor Lane<br>Suite B-2<br>Dover, NH 03820<br><br>
    Online: Inquiry Form<br>Tel: 555-214-3090<br>Fax: 555-214-3091<br>
    <span class="email">Email: info@brevardtradepartners.com</span>
  </div>
</footer>

<div class="bottom-bar">
  <p class="copyright">© 2015 Brevard Trade Partners, LLC. | USA – Hong Kong – Taipei</p>
  <span class="social" style="left:962px"></span>
  <span class="social" style="left:999px"></span>
  <span class="social" style="left:1037px"></span>
  <span class="social" style="left:1071px"></span>
</div>

</body>
</html>
```